Awesome Business Card Design needed!

Hey there.
I'm looking for a simple but awesome business card design.
Type of company: Online advertisement agency
(please don't use the typical business people or statistics images on the card)
The front has to display the business name
and possibly some sort of logo ( perhaps something with the two M's of the biz name )
And the back of the card should say:
Name
Phone
Email
Let your imagination flow.
here are some designs that I like and that you can use as inspiration.
Simple but Awesome
http://images.lumavexo.com/designs/55128_877673_43091_thumbnail.jpg
http://images.lumavexo.com/designs/37714_747642_40106_image.jpg
http://images.lumavexo.com/designs/55128_877673_43091_image.jpg
http://images.lumavexo.com/designs/51321_781878_43091_image.jpg
http://images.lumavexo.com/designs/33378_399063_15912_image.jpg
http://images.lumavexo.com/designs/2337_271604_9495_image.jpg
good luck

```html
<!DOCTYPE html>
<html lang="en">
<head>
<meta charset="utf-8">
<title>Veldora Media – Business Card</title>
<link rel="stylesheet" href="https://fonts.googleapis.com/css2?family=Questrial&display=swap">
<style>
  :root {
    --canvas-bg: #f2f2f2;
    --card-dark: #0c0c0c;
    --card-mid: #1a1a1a;
    --card-light: #3a3a3a;
    --ink-light: #ffffff;
    --card-shadow: rgba(0, 0, 0, 0.22);
  }
  * { margin: 0; padding: 0; box-sizing: border-box; }
  html, body {
    width: 1200px;
    height: 1200px;
    overflow: hidden;
    background: var(--canvas-bg);
  }
  .canvas {
    position: relative;
    width: 1200px;
    height: 1200px;
    display: flex;
    flex-direction: column;
    align-items: center;
    justify-content: center;
    gap: 80px;
  }
  .card {
    position: relative;
    width: 760px;
    height: 434px;
    background: linear-gradient(135deg, var(--card-dark) 0%, var(--card-mid) 55%, var(--card-light) 100%);
    box-shadow: 0 14px 36px var(--card-shadow);
    font-family: "Questrial", "Century Gothic", sans-serif;
    color: var(--ink-light);
  }
  .card-front {
    display: flex;
    align-items: center;
    justify-content: center;
  }
  .brand-name {
    font-size: 64px;
    font-weight: 400;
    letter-spacing: 1px;
    line-height: 1;
    margin-top: -20px;
  }
  .card-back .contact {
    position: absolute;
    left: 66px;
    top: 176px;
    font-size: 31px;
    line-height: 1.05;
    letter-spacing: 0.5px;
    list-style: none;
  }
  .contact .contact-name { padding-left: 5px; }
</style>
</head>
<body>
  <main class="canvas">
    <section class="card card-front" aria-label="Card front">
      <h1 class="brand-name">VELDORA MEDIA</h1>
    </section>
    <section class="card card-back" aria-label="Card back">
      <ul class="contact">
        <li class="contact-name">marketer name</li>
        <li class="contact-phone">000 000 0000</li>
        <li class="contact-email">name@veldoramedia.com</li>
      </ul>
    </section>
  </main>
</body>
</html>
```